Modern Verdell Tree Care Website

I need a website for a full service Tree Care company. The company provides tree pruning, tree removal, tree preservation, emergency services, stump grinding, and emergency tree services.

Target Market(s)

Customers that need tree services

Industry/Entity Type

Landscaping, Tree Services

Coding

Coded - Design and coding required

Number of Pages Required

5+ page

Font styles to use
Sans Serif

Requirements
Must have
• Good clean design that showcases the services the company provides.
Nice to have
• Services page; contact form, blog, home page, about page

```html
<!DOCTYPE html>
<html lang="en">
<head>
<meta charset="utf-8">
<title>Verdell Tree Care</title>
<link href="https://fonts.googleapis.com/css2?family=Fira+Sans:wght@400;500;600;700&family=Open+Sans:wght@400;600;700&display=swap" rel="stylesheet">
<style>
:root{
  --navy:#101b4d;
  --navy-deep:#0d1533;
  --navy-bar:#1c2547;
  --green:#7cc242;
  --green-dark:#5e9c2c;
  --orange:#f7a531;
  --ink:#2a2f45;
  --muted:#7d8497;
  --pale:#f3f7fa;
  --field:#eef2f8;
  --white:#ffffff;
}
*{box-sizing:border-box;margin:0;padding:0}
html,body{width:1200px;height:4733px;overflow:hidden}
body{position:relative;font-family:"Open Sans",sans-serif;color:var(--ink);background:var(--white)}
.abs{position:absolute}

/* header */
.site-header{position:absolute;top:0;left:0;width:1200px;height:88px;background:var(--white);border-bottom:1px solid #e6e6e6;z-index:5}
.topbar{position:absolute;top:0;left:0;width:1200px;height:36px;background:#f2f2f2}
.logo-badge{position:absolute;left:148px;top:4px;width:160px;height:92px;background:var(--white);border-radius:50%;box-shadow:0 4px 10px rgba(0,0,0,.12);z-index:6;display:flex;align-items:center;justify-content:center;gap:6px}
.logo-badge .mark{width:14px;height:14px;background:var(--green)}
.logo-badge .name{font-family:"Fira Sans",sans-serif;font-weight:700;font-size:15px;color:var(--navy);line-height:1.1;width:100px}
.welcome{left:337px;top:9px;font-size:12px;font-weight:600;color:var(--ink)}
.top-divider{left:590px;top:6px;width:1px;height:22px;background:#bbb}
.mail-chip{left:626px;top:4px;width:26px;height:26px;border-radius:50%;border:1.5px solid var(--green);display:flex;align-items:center;justify-content:center}
.top-mail{left:662px;top:9px;font-size:11px;color:var(--ink)}
.main-nav a{position:absolute;font-size:12px;font-weight:600;color:var(--ink);text-decoration:none;white-space:nowrap}
.main-nav{left:336px;top:53px}
.main-nav a.active{color:#c0392b}
.call-box{left:877px;top:0;width:160px;height:88px;background:var(--green);color:var(--white);padding:18px 0 0 26px}
.call-box small{display:block;font-size:13px}
.call-box strong{display:block;font-size:18px;font-weight:400;margin-top:6px;white-space:nowrap}
.call-icon{left:858px;top:26px;width:34px;height:34px;border-radius:50%;background:var(--white);border:2px solid var(--green);display:flex;align-items:center;justify-content:center;z-index:7}

/* hero */
.hero{top:88px;left:0;width:1200px;height:707px;background:linear-gradient(90deg,#0b0f0b 0%,#1f2a1a 28%,#3d5224 55%,#5c7434 75%,#46602a 100%)}
.hero-tag{left:153px;top:218px;height:42px;width:202px;background:rgba(10,14,25,.85);border-left:4px solid var(--green);color:var(--white);font-size:16px;font-weight:600;padding:10px 16px}
.hero-title{left:153px;top:290px;font-family:"Fira Sans",sans-serif;font-weight:600;font-size:48px;color:var(--white);letter-spacing:1px}
.hero-text{left:154px;top:362px;width:470px;font-size:16px;line-height:26px;color:#e8e8e8}
.btn{display:flex;align-items:center;justify-content:center;gap:12px;background:var(--green);color:var(--white);font-weight:700;font-size:15px}
.hero-btn{left:153px;top:462px;width:176px;height:48px}

/* about */
.about-ring{left:114px;top:928px;width:446px;height:446px;border-radius:50%;border:2px solid #1f8fc7}
.about-photo{left:134px;top:948px;width:422px;height:422px;border-radius:50%;background:radial-gradient(circle at 40% 40%,#8a7a54 0%,#55623a 45%,#2c3a20 100%)}
.about-small{left:370px;top:1168px;width:202px;height:202px;border-radius:50%;background:radial-gradient(circle,#3f4a5c 0%,#23293a 100%);border:4px solid var(--white)}
.eyebrow{font-size:12px;font-weight:600;color:var(--green);letter-spacing:.3px}
.sec-title{font-family:"Fira Sans",sans-serif;font-weight:600;color:var(--navy);font-size:41px;line-height:51px}
.about-eyebrow{left:622px;top:944px}
.about-title{left:621px;top:978px;width:450px}
.about-sub{left:622px;top:1108px;font-size:21px;font-weight:500;color:var(--navy);font-family:"Fira Sans",sans-serif}
.about-text{left:622px;width:500px;font-size:12.5px;line-height:21px;color:var(--muted)}
.about-btn{left:620px;top:1312px;width:154px;height:43px;font-size:15px}

/* why */
.why{top:1480px;left:0;width:1200px;height:630px;background:var(--pale);overflow:hidden}
.why-photo{right:0;top:0;width:780px;height:630px;background:linear-gradient(90deg,rgba(243,247,250,1) 0%,rgba(200,220,175,.9) 30%,#9bbd66 60%,#6e9437 85%,#577b2a 100%)}
.why-eyebrow{left:123px;top:93px}
.why-title{left:123px;top:130px;width:420px}
.why-item{left:123px;width:520px;height:62px}
.why-icon{position:absolute;left:0;top:0;width:62px;height:62px;border-radius:50%;background:var(--white);box-shadow:0 3px 10px rgba(0,0,0,.08);display:flex;align-items:center;justify-content:center}
.why-item h4{position:absolute;left:75px;top:12px;font-size:15px;font-weight:700;color:var(--navy);white-space:nowrap}
.why-item p{position:absolute;left:75px;top:32px;font-size:12.5px;color:var(--muted);white-space:nowrap}

/* services */
.svc-eyebrow{top:2220px;left:0;width:1200px;text-align:center}
.svc-title{top:2256px;left:0;width:1200px;text-align:center}
.svc-card{top:2371px;width:304px;height:322px;border-radius:22px;overflow:hidden}
.svc-card h3{position:absolute;left:25px;bottom:26px;font-family:"Fira Sans",sans-serif;font-weight:600;font-size:21px;color:var(--white)}
.card-pruning{left:119px;background:linear-gradient(160deg,#5c7b3a 0%,#7e8f66 45%,#3f4d2c 100%)}
.card-removal{left:447px;background:linear-gradient(160deg,#6ea43a 0%,#3f7a25 60%,#2c5a1a 100%)}
.card-grinding{left:774px;background:linear-gradient(160deg,#7e9a56 0%,#5d7e3e 55%,#3d5527 100%)}
.card-removal .inner{position:absolute;left:24px;top:128px;width:250px}
.card-removal h4{font-family:"Fira Sans",sans-serif;font-weight:600;font-size:21px;color:var(--white)}
.card-removal p{margin-top:12px;font-size:8.5px;line-height:15px;color:#eef5e5}
.card-removal .mini-btn{margin-top:16px;width:106px;height:29px;font-size:10px}

/* testimonials */
.testi{top:2794px;left:0;width:1200px;height:650px;background:var(--pale);overflow:hidden}
.testi-eyebrow{left:0;top:66px;width:1200px;text-align:center}
.testi-title{left:0;top:100px;width:1200px;text-align:center}
.testi-board{left:158px;top:174px;width:882px;height:294px;background:var(--white);border-top:3px solid var(--green);box-shadow:0 4px 16px rgba(0,0,0,.05);display:flex}
.testi-col{flex:1;text-align:center;padding-top:32px;border-right:1px solid #ececec;position:relative}
.testi-col:last-child{border-right:none}
.quote-mark{height:24px;display:flex;justify-content:center}
.testi-col h4{margin-top:10px;font-size:16px;font-weight:700;color:var(--ink)}
.testi-col .role{font-size:9px;color:#3a6ed1;letter-spacing:.5px;margin-top:3px}
.testi-col p{margin:14px auto 0;width:220px;font-size:12.5px;line-height:23px;color:var(--muted)}
.pointer{position:absolute;bottom:-20px;left:50%;margin-left:-20px;width:0;height:0;border-left:20px solid transparent;border-right:20px solid transparent;border-top:20px solid var(--white)}
.avatar{width:60px;height:60px;border-radius:50%;top:512px}

/* quote */
.quote-art{left:190px;top:3555px;width:470px;height:510px;border-radius:46% 54% 40% 60%/55% 45% 55% 45%;background:linear-gradient(160deg,#e4e6ea 0%,#cdbf8e 35%,#1f8c8a 70%,#17366b 100%)}
.q-kicker{left:728px;top:3578px;font-family:"Fira Sans",sans-serif;font-size:27px;color:var(--ink)}
.q-title{left:728px;top:3617px;font-family:"Fira Sans",sans-serif;font-size:35px;color:var(--green)}
.q-title b{color:var(--navy);font-weight:600}
.f-label{left:728px;font-size:11.5px;font-weight:700;color:var(--ink)}
.f-field{left:728px;width:344px;background:var(--field);font-size:11px;color:#8a90a3;padding:0 22px;display:flex;align-items:center;justify-content:space-between}
.f-field.active{background:var(--white);border:1.5px solid var(--green)}
.q-send{left:924px;top:4021px;width:148px;height:41px;font-size:11px}

/* footer */
.footer{top:4167px;left:0;width:1200px;height:513px;background:var(--navy-deep)}
.f-logo{left:86px;top:90px;display:flex;align-items:center;gap:12px}
.f-logo .mark{width:24px;height:24px;background:var(--white)}
.f-logo .name{font-family:"Fira Sans",sans-serif;font-weight:700;font-size:28px;color:var(--white)}
.f-phone{left:86px;top:153px;font-size:19px;font-weight:700;color:var(--white)}
.f-cta{left:86px;top:181px;font-size:14px;font-weight:600;color:var(--green)}
.f-about{left:86px;top:219px;width:290px;font-size:14px;line-height:24px;color:#d5d9e6}
.f-more{left:86px;top:303px;font-size:14px;font-weight:700;color:var(--white)}
.f-head{font-family:"Fira Sans",sans-serif;font-size:22px;font-weight:600;color:var(--white)}
.f-rule{width:40px;height:3px;background:var(--green)}
.f-links{list-style:none}
.f-links li{height:30px;font-size:14px;color:#d5d9e6;display:flex;align-items:center;gap:10px}
.f-links li::before{content:"→";color:#aab0c6;font-size:13px}
.f-news{left:787px;top:175px;width:320px;font-size:12.5px;line-height:26px;color:#aeb4c8}
.f-input{left:787px;top:244px;width:270px;height:47px;background:#161f44;font-size:12px;color:#9aa1b8;padding:0 22px;display:flex;align-items:center}
.f-go{left:1057px;top:244px;width:51px;height:47px;background:var(--green);display:flex;align-items:center;justify-content:center}
.info-bar{left:86px;top:419px;width:1026px;height:86px;background:var(--navy-bar);border-radius:4px;display:flex}
.info-cell{flex:1;display:flex;align-items:center;gap:22px;padding-left:28px;border-right:1px solid #3a4266}
.info-cell:last-child{border-right:none}
.info-cell h5{font-size:14px;font-weight:700;color:var(--white)}
.info-cell p{font-size:14.5px;color:#d5d9e6;margin-top:4px;white-space:nowrap}
.to-top{left:1125px;top:4645px;width:48px;height:48px;background:var(--green);display:flex;align-items:center;justify-content:center;z-index:3}
.legal{top:4680px;left:0;width:1200px;height:53px;background:var(--white)}
.legal .copy{left:86px;top:27px;font-size:12.5px;color:var(--ink)}
.legal .links{left:800px;top:27px;font-size:12.5px;color:var(--ink);display:flex;gap:26px}
</style>
</head>
<body>

<header class="site-header">
  <div class="topbar"></div>
  <div class="abs welcome">WELCOME TO THIS COMPANY</div>
  <div class="abs top-divider"></div>
  <div class="abs mail-chip">
    <svg width="14" height="10" viewBox="0 0 14 10"><rect x=".5" y=".5" width="13" height="9" fill="none" stroke="#7cc242"/><path d="M.5 .5L7 6l6.5-5.5" fill="none" stroke="#7cc242"/></svg>
  </div>
  <div class="abs top-mail">info@verdelltree.com</div>
  <nav class="abs main-nav">
    <a class="active" style="left:0">HOME</a>
    <a style="left:87px">SERVICES</a>
    <a style="left:181px">ABOUT US</a>
    <a style="left:281px">PROJECTS</a>
    <a style="left:402px">LOGIN</a>
  </nav>
  <div class="abs call-icon">
    <svg width="16" height="16" viewBox="0 0 24 24"><path d="M6.6 10.8a15 15 0 006.6 6.6l2.2-2.2a1 1 0 011-.25 11.4 11.4 0 003.6.6 1 1 0 011 1V20a1 1 0 01-1 1A17 17 0 013 4a1 1 0 011-1h3.5a1 1 0 011 1c0 1.25.2 2.45.6 3.6a1 1 0 01-.25 1z" fill="#7cc242"/></svg>
  </div>
  <div class="abs call-box"><small>Call us today at</small><strong>(555) 201-7384</strong></div>
</header>
<div class="logo-badge"><span class="mark"></span><span class="name">Verdell Tree Care</span></div>

<section class="abs hero" role="img" aria-label="Arborist in climbing gear cutting a large tree trunk in a green forest">
  <div class="abs hero-tag">We are leaders in</div>
  <h1 class="abs hero-title">Tree Care</h1>
  <p class="abs hero-text">Lorem ipsum dolor sit amet, consectetur adipiscing elit, sed do eiusmod tempor incididunt ut labore et dolore magna aliqua.</p>
  <div class="abs btn hero-btn">Read More</div>
</section>

<section class="about">
  <div class="abs about-ring"></div>
  <div class="abs about-photo" role="img" aria-label="Tree worker in a harness sawing branches high in a tree"></div>
  <div class="abs about-small" role="img" aria-label="Climber ascending a tree trunk on ropes"></div>
  <div class="abs eyebrow about-eyebrow">WHO WE ARE</div>
  <h2 class="abs sec-title about-title">We Offer Sustainable Tree Solutions</h2>
  <h3 class="abs about-sub">Enhancing Landscapes, One Tree at a Time</h3>
  <p class="abs about-text" style="top:1152px">Lorem ipsum dolor sit amet, consectetur adipiscing elit, sed do eiusmod temp or incididunt ut labore et dolore magna aliqua. Ut enim ad minim veniam, quis laboris nisi ut aliquip ex ea commodo consequat.</p>
  <p class="abs about-text" style="top:1230px">Lorem ipsum dolor sit amet, consectetur adipiscing elit, sed do eiusmod temp or incididunt ut labore et dolore magna aliqua.</p>
  <div class="abs btn about-btn">Contact us
    <svg width="16" height="12" viewBox="0 0 16 12"><path d="M1 6h13M9 1l5 5-5 5" fill="none" stroke="#fff" stroke-width="1.6"/></svg>
  </div>
</section>

<section class="abs why">
  <div class="abs why-photo" role="img" aria-label="Hands holding a small tree growing in soil with soft green light behind"></div>
  <svg class="abs" style="left:0;top:0" width="1200" height="630" viewBox="0 0 1200 630">
    <path d="M0 0H1200V80C1000 20 700 -5 0 0Z" fill="#ffffff"/>
    <path d="M760 2C950 8 1100 40 1200 80V115C1120 60 980 20 760 2Z" fill="#f7a531"/>
    <path d="M0 630H1200V600C900 630 500 640 0 560Z" fill="#ffffff"/>
    <path d="M0 515C250 600 600 625 1200 600C700 650 300 620 0 560Z" fill="#7cc242"/>
  </svg>
  <div class="abs eyebrow why-eyebrow">WHY CHOOSE US</div>
  <h2 class="abs sec-title why-title">Your Tree Care Professionals</h2>
  <div class="abs why-item" style="top:242px">
    <div class="why-icon"><svg width="24" height="24" viewBox="0 0 24 24" fill="none" stroke="#7cc242" stroke-width="1.5"><circle cx="10" cy="7" r="4"/><path d="M3 21c0-4 3-7 7-7M15 15l2 2 4-4"/></svg></div>
    <h4>On-Time Appointments</h4><p>Inventore veritatis uasvitae dicta suntetur sipid</p>
  </div>
  <div class="abs why-item" style="top:326px">
    <div class="why-icon"><svg width="24" height="24" viewBox="0 0 24 24" fill="none" stroke="#7cc242" stroke-width="1.5"><path d="M4 14v-2a8 8 0 0116 0v2"/><rect x="3" y="14" width="4" height="6" rx="1"/><rect x="17" y="14" width="4" height="6" rx="1"/></svg></div>
    <h4>Proven Record</h4><p>Inventore veritatis uasvitae dicta suntetur sipid</p>
  </div>
  <div class="abs why-item" style="top:410px">
    <div class="why-icon"><svg width="24" height="24" viewBox="0 0 24 24" fill="none" stroke="#7cc242" stroke-width="1.5"><path d="M12 3l2.7 5.6 6.1.9-4.4 4.3 1 6.1L12 17l-5.4 2.9 1-6.1L3.2 9.5l6.1-.9z"/></svg></div>
    <h4>Professionalism and Expertise</h4><p>Inventore veritatis uasvitae dicta suntetur sipid</p>
  </div>
</section>

<section class="services">
  <div class="abs eyebrow svc-eyebrow">OUR SERVICES</div>
  <h2 class="abs sec-title svc-title">Services We Provide</h2>
  <article class="abs svc-card card-pruning" role="img" aria-label="Worker trimming branches with long-handled pruning shears">
    <h3>Tree Pruning</h3>
  </article>
  <article class="abs svc-card card-removal" aria-label="Tree removal service">
    <div class="inner">
      <h4>Tree Removal</h4>
      <p>Lorem ipsum dolor sit amet, consectetur adipiscing elit, sed do eiusmod tempor incididunt ut labore et dolore magna aliqua. Ut enim ad minim veniam, quis laboris nisi ut a liquip ex ea commodo consequat. Lorem</p>
      <div class="btn mini-btn">Contact us
        <svg width="12" height="9" viewBox="0 0 16 12"><path d="M1 6h13M9 1l5 5-5 5" fill="none" stroke="#fff" stroke-width="1.8"/></svg>
      </div>
    </div>
  </article>
  <article class="abs svc-card card-grinding" role="img" aria-label="Two gardeners tending hedges along a green garden path">
    <h3>Stump Grinding</h3>
  </article>
</section>

<section class="abs testi">
  <svg class="abs" style="left:0;top:0" width="1200" height="650" viewBox="0 0 1200 650">
    <path d="M0 0H1200V90C1000 25 700 0 0 0Z" fill="#ffffff"/>
    <path d="M760 4C950 12 1100 45 1200 90V122C1120 68 980 25 760 4Z" fill="#f7a531"/>
    <path d="M0 650H1200V620C900 650 500 650 0 575Z" fill="#ffffff"/>
    <path d="M0 520C250 610 600 640 1200 620C700 660 300 640 0 575Z" fill="#7cc242"/>
  </svg>
  <div class="abs eyebrow testi-eyebrow">OUR SERVICES</div>
  <h2 class="abs sec-title testi-title">What Clients are Saying</h2>
  <div class="abs testi-board">
    <div class="testi-col"><div class="quote-mark"><svg width="32" height="22" viewBox="0 0 32 22" fill="none" stroke="#7cc242" stroke-width="2"><path d="M2 20V12C2 6 5 2 12 1M18 20V12c0-6 3-10 10-11"/><rect x="2" y="11" width="10" height="9"/><rect x="18" y="11" width="10" height="9"/></svg></div><h4>Dorian Welles</h4><div class="role">CLIENT</div><p>Lorem ipsum dolor sit amet, cons ectetur adipiscing elit, sed do eius mod tempor incididunt ut labore et dolore magna aliqua.</p><span class="pointer"></span></div>
    <div class="testi-col"><div class="quote-mark"><svg width="32" height="22" viewBox="0 0 32 22" fill="none" stroke="#7cc242" stroke-width="2"><path d="M2 20V12C2 6 5 2 12 1M18 20V12c0-6 3-10 10-11"/><rect x="2" y="11" width="10" height="9"/><rect x="18" y="11" width="10" height="9"/></svg></div><h4>Dorian Welles</h4><div class="role">CLIENT</div><p>Lorem ipsum dolor sit amet, cons ectetur adipiscing elit, sed do eius mod tempor incididunt ut labore et dolore magna aliqua.</p><span class="pointer"></span></div>
    <div class="testi-col"><div class="quote-mark"><svg width="32" height="22" viewBox="0 0 32 22" fill="none" stroke="#7cc242" stroke-width="2"><path d="M2 20V12C2 6 5 2 12 1M18 20V12c0-6 3-10 10-11"/><rect x="2" y="11" width="10" height="9"/><rect x="18" y="11" width="10" height="9"/></svg></div><h4>Dorian Welles</h4><div class="role">CLIENT</div><p>Lorem ipsum dolor sit amet, cons ectetur adipiscing elit, sed do eius mod tempor incididunt ut labore et dolore magna aliqua.</p><span class="pointer"></span></div>
  </div>
  <div class="abs avatar" style="left:279px;background:#4a5a6e" role="img" aria-label="Client portrait"></div>
  <div class="abs avatar" style="left:569px;background:#3b3f52" role="img" aria-label="Client portrait"></div>
  <div class="abs avatar" style="left:861px;background:#9a9da6" role="img" aria-label="Client portrait"></div>
</section>

<section class="quote">
  <div class="abs quote-art" role="img" aria-label="Two smiling engineers in hard hats and safety vests holding plans, set on a teal shape with small decorative accents"></div>
  <div class="abs q-kicker">Get A Quote</div>
  <div class="abs q-title"><b>Free</b> Consultations</div>
  <div class="abs f-label" style="top:3684px">Full Name Here</div>
  <div class="abs f-field active" style="top:3709px;height:50px">Jonas R. Mabry
    <svg width="12" height="12" viewBox="0 0 12 12" fill="none" stroke="#f7a531"><circle cx="6" cy="4" r="2.5"/><path d="M1.5 11c0-2.5 2-4 4.5-4s4.5 1.5 4.5 4"/></svg>
  </div>
  <div class="abs f-label" style="top:3786px">I Would LikeTo Discuss</div>
  <div class="abs f-field" style="top:3810px;height:50px">I'm Talking About</div>
  <div class="abs f-label" style="top:3887px">Leave A Message</div>
  <div class="abs f-field" style="top:3911px;height:92px;align-items:flex-start;padding-top:20px">Write Message
    <svg width="12" height="9" viewBox="0 0 14 10"><rect x=".5" y=".5" width="13" height="9" fill="none" stroke="#555"/><path d="M.5 .5L7 6l6.5-5.5" fill="none" stroke="#555"/></svg>
  </div>
  <div class="abs btn q-send">Send Message</div>
</section>

<footer class="abs footer">
  <div class="abs f-logo"><span class="mark"></span><span class="name">Verdell Tree Care</span></div>
  <div class="abs f-phone">800-555-0142</div>
  <div class="abs f-cta">Call for free consultation</div>
  <p class="abs f-about">Lorem ipsum dolor sit amet, cons ectetur adipiscing elit, sed do eius mod tempor incididunt</p>
  <div class="abs f-more">Read more →</div>

  <div class="abs f-head" style="left:437px;top:77px">Useful Links</div>
  <div class="abs f-rule" style="left:437px;top:118px"></div>
  <ul class="abs f-links" style="left:437px;top:146px">
    <li>About Company</li><li>Leadership</li><li>Blog Post</li><li>FAQ's</li><li>Certification</li><li>Testimonials</li>
  </ul>
  <ul class="abs f-links" style="left:603px;top:146px">
    <li>Services</li><li>Industries</li><li>Feedback</li><li>Partners</li><li>Pricing</li><li>Contact</li>
  </ul>

  <div class="abs f-head" style="left:790px;top:77px">Newsletter</div>
  <div class="abs f-rule" style="left:790px;top:118px"></div>
  <p class="abs f-news">Don't miss to subscribe to our new feeds, kindly fill the form below.</p>
  <div class="abs f-input">Your Email Address</div>
  <div class="abs f-go"><svg width="18" height="14" viewBox="0 0 16 12"><path d="M1 6h13M9 1l5 5-5 5" fill="none" stroke="#fff" stroke-width="1.6"/></svg></div>

  <div class="abs info-bar">
    <div class="info-cell">
      <svg width="28" height="36" viewBox="0 0 24 30" fill="none" stroke="#7cc242" stroke-width="1.6"><path d="M12 28S3 17 3 11a9 9 0 0118 0c0 6-9 17-9 17z"/><circle cx="12" cy="11" r="3.5"/></svg>
      <div><h5>Location</h5><p>18 Birchwood Ln, NY 10512</p></div>
    </div>
    <div class="info-cell">
      <svg width="34" height="28" viewBox="0 0 34 28" fill="none" stroke="#7cc242" stroke-width="1.6"><rect x="1" y="4" width="32" height="22"/><path d="M1 4l16 12L33 4"/></svg>
      <div><h5>Mail us</h5><p>support@verdelltree.com</p></div>
    </div>
    <div class="info-cell">
      <svg width="32" height="32" viewBox="0 0 32 32" fill="none" stroke="#7cc242" stroke-width="1.6"><circle cx="16" cy="16" r="13"/><path d="M16 8v8l6 4"/></svg>
      <div><h5>Office hrs</h5><p>9.00am to 7.00pm (mon-Sat)</p></div>
    </div>
  </div>
</footer>
<div class="abs to-top"><svg width="14" height="18" viewBox="0 0 14 18"><path d="M7 17V2M1 8l6-6 6 6" fill="none" stroke="#fff" stroke-width="1.6"/></svg></div>

<div class="abs legal">
  <div class="abs copy">Verdell Tree Care</div>
  <div class="abs links"><span>Privacy Policy</span><span>Terms &amp; Conditions</span><span>Site Map</span></div>
</div>

</body>
</html>
```